Otter Bites Guild - A Monthly Subscription Dog Treats Club - Shopify Website Design

A monthly subscription company. Need a Shopify Website Design and uploaded to fully work with Crisp Renewals.

Please look at these sites for examples as well as the images I enclosed.

https://www.mealbrightly.com/
https://www.globalmunchbox.com/

Number of Pages Required

1 page

```html
<!DOCTYPE html>
<html lang="en">
<head>
<meta charset="utf-8">
<title>Otter Bites Guild – Monthly Dog Treats Club</title>
<link href="https://fonts.googleapis.com/css2?family=Lato:wght@300;400;700;900&display=swap" rel="stylesheet">
<style>
:root{
  --brand-blue:#1f66a3;
  --step-blue:#2c6fae;
  --orange:#ff6a0d;
  --sky:#55bfee;
  --hero-a:#1e8fd0;
  --hero-b:#3db1ea;
  --panel:#f2f2f2;
  --ink:#222;
  --body:#333;
  --dark:#121212;
  --white:#fff;
}
*{box-sizing:border-box;margin:0;padding:0}
html,body{width:1200px;height:3733px;overflow:hidden}
body{font-family:"Lato",sans-serif;color:var(--body);background:var(--white);position:relative}
.abs{position:absolute}
a{color:inherit;text-decoration:none}

/* top bar */
.topbar{left:0;top:0;width:1200px;height:90px;background:var(--panel)}
.logo{left:77px;top:30px;font-size:25px;font-weight:700;color:var(--brand-blue)}
.search{left:345px;top:25px;width:467px;height:40px;background:var(--white);border:1px solid #e2e2e2;font-size:14px;color:#555;padding:11px 12px}
.search-btn{left:812px;top:25px;width:43px;height:40px;background:var(--brand-blue)}
.account{left:949px;top:34px;font-size:14px;color:var(--ink)}
.account span{margin:0 12px}

/* nav */
.nav{left:0;top:90px;width:1200px;height:98px;background:var(--white);border-bottom:1px solid #e6e6e6}
.nav a{position:absolute;top:42px;font-size:17px;font-weight:700;color:var(--ink)}
.nav a.active{color:var(--brand-blue)}

/* hero */
.hero{left:0;top:188px;width:1200px;height:586px;background:linear-gradient(100deg,var(--hero-a),var(--hero-b))}
.hero-photo{left:470px;top:188px;width:730px;height:586px;background:linear-gradient(90deg,rgba(61,177,234,0),rgba(150,120,80,.55))}
.hero h1{left:74px;top:360px;font-size:68px;font-weight:900;color:var(--white);line-height:1}
.hero-sub{left:74px;top:448px;font-size:28px;font-weight:700;color:var(--white);line-height:35px}
.btn{background:var(--orange);color:var(--white);font-weight:700;text-align:center}
.hero-btn{left:74px;top:542px;width:180px;height:43px;font-size:18px;line-height:43px}

/* steps */
.step{top:853px;width:330px;height:193px;background:var(--panel)}
.step svg{position:absolute;left:27px;top:45px}
.step-text{position:absolute;left:129px;top:42px}
.step-num{font-size:18px;font-weight:700;color:var(--step-blue)}
.step-title{font-size:18px;font-weight:700;color:var(--orange);margin-top:8px}
.step-body{font-size:16px;color:var(--body);line-height:25px;margin-top:8px}

/* sections */
.section-title{font-size:36px;font-weight:700;color:var(--brand-blue);line-height:43px}
.copy{font-size:16px;line-height:32.5px;color:var(--body)}
.welcome-img{left:72px;top:1140px;width:471px;height:418px;background:linear-gradient(135deg,#d9a877,#b88657 60%,#c9954f)}
.welcome-title{left:617px;top:1172px}
.welcome-copy{left:616px;top:1277px;width:520px}
.welcome-btn{left:616px;top:1463px;width:149px;height:57px;font-size:17px;line-height:57px}

.tile{top:1672px;width:242px;height:299px}
.tile-label{position:absolute;left:23px;bottom:15px;width:196px;height:43px;background:var(--brand-blue);color:var(--white);font-size:23px;font-weight:700;text-align:center;line-height:43px}

.inside-img{left:616px;top:2050px;width:584px;height:482px;background:linear-gradient(135deg,#f3f3f3,#dcdcdc)}
.inside-title{left:74px;top:2113px}
.inside-copy{left:74px;top:2218px;width:520px}
.inside-btn{left:74px;top:2404px;width:255px;height:56px;font-size:17px;line-height:56px}

/* newsletter */
.newsletter{left:74px;top:2621px;width:1052px;height:344px;background:var(--sky)}
.news-img{left:43px;top:2650px;width:410px;height:315px;background:radial-gradient(ellipse at 55% 45%,#4a4a4a,#9a9a9a 55%,rgba(85,191,238,0) 72%)}
.news-title{left:510px;top:2687px;font-size:35px;font-weight:300;color:var(--white)}
.news-copy{left:510px;top:2746px;width:600px;font-size:16px;line-height:28px;color:var(--white)}
.news-input{left:510px;top:2834px;width:442px;height:58px;background:var(--white);font-size:16px;color:var(--ink);padding:19px 16px}
.news-btn{left:952px;top:2834px;width:146px;height:58px;font-size:17px;line-height:58px}

/* footer */
.footer{left:0;top:3021px;width:1200px;height:396px;background:var(--panel)}
.foot-col{top:3078px}
.foot-col h3{font-size:23px;font-weight:700;color:var(--ink);margin-bottom:14px}
.foot-col li{list-style:none;font-size:16px;color:var(--ink);line-height:38.7px}
.foot-col p{font-size:16px;line-height:27.5px;color:var(--ink);width:230px}
.socials{left:884px;top:3127px;display:flex;gap:12px}
.socials span{width:48px;height:48px;border:2px solid #666;border-radius:50%;display:block}

/* legal */
.legal{left:0;top:3417px;width:1200px;height:316px;background:var(--dark)}
.legal-links{left:0;top:3468px;width:1200px;text-align:center;font-size:16px;color:#ddd}
.legal-links span{margin:0 14px;color:#aaa}
.currency{left:532px;top:3524px;width:136px;height:42px;border:1px solid #444;color:#ddd;font-size:14px;padding:13px 14px}
.pay{left:362px;top:3591px;display:flex;gap:5px}
.pay span{width:43px;height:26px;background:var(--white);border-radius:3px;display:block}
.copyright{left:0;top:3662px;width:1200px;text-align:center;font-size:15px;color:#ddd}
</style>
</head>
<body>

<header>
  <div class="abs topbar"></div>
  <div class="abs logo">Otter Bites Guild</div>
  <div class="abs search">Search</div>
  <div class="abs search-btn">
    <svg width="43" height="40" viewBox="0 0 43 40"><circle cx="20" cy="19" r="5" fill="none" stroke="#fff" stroke-width="2"/><line x1="24" y1="23" x2="27" y2="26" stroke="#fff" stroke-width="2.4"/></svg>
  </div>
  <div class="abs account">Sign in<span>|</span>Create account</div>
  <nav class="abs nav">
    <a class="active" style="left:212px">Home</a>
    <a style="left:316px">About Us</a>
    <a style="left:446px">How &nbsp;it Works</a>
    <a style="left:614px">Subscription Plan</a>
    <a style="left:809px">Blog</a>
    <a style="left:901px">Contact Us</a>
  </nav>
</header>

<section>
  <div class="abs hero" role="img" aria-label="Blue-toned photo of a dog holding a box of treats beside an open box of chews"></div>
  <div class="abs hero-photo" role="img" aria-label="Dog with a treat box"></div>
  <div class="abs hero"><h1 class="abs" style="left:74px;top:172px">Otter Bites Guild</h1>
  <div class="abs hero-sub" style="left:74px;top:260px">We are a Monthly Subscription<br>Dog Treats Club.</div>
  <a class="abs btn hero-btn" style="left:74px;top:354px">Subscribe Now</a></div>
</section>

<section>
  <div class="abs step" style="left:74px">
    <svg width="66" height="84" viewBox="0 0 66 84"><rect x="3" y="8" width="60" height="74" rx="3" fill="#fff" stroke="#d2312b" stroke-width="4"/><rect x="20" y="2" width="26" height="12" rx="2" fill="#1f66a3"/><g stroke="#333" stroke-width="3"><path d="M14 30l4 4 7-8M14 48l4 4 7-8M14 66l4 4 7-8"/><line x1="32" y1="31" x2="52" y2="31"/><line x1="32" y1="49" x2="52" y2="49"/><line x1="32" y1="67" x2="52" y2="67"/></g></svg>
    <div class="step-text"><div class="step-num">STEP 1</div><div class="step-title">CRAS VIVERRAM</div><div class="step-body">Neque porro quisquam<br>est qui dolorem</div></div>
  </div>
  <div class="abs step" style="left:435px">
    <svg width="66" height="84" viewBox="0 0 66 84"><rect x="6" y="2" width="44" height="10" fill="#d2312b"/><rect x="4" y="12" width="48" height="70" rx="4" fill="#f7a21b" stroke="#333" stroke-width="3"/><circle cx="28" cy="48" r="10" fill="#333"/><rect x="44" y="70" width="20" height="12" fill="#555"/></svg>
    <div class="step-text"><div class="step-num">STEP 2</div><div class="step-title">CRAS VIVERRAM</div><div class="step-body">Neque porro quisquam<br>est qui dolorem</div></div>
  </div>
  <div class="abs step" style="left:796px">
    <div class="abs" role="img" aria-label="Illustration of a dog with a bone" style="left:18px;top:45px;width:95px;height:84px;background:linear-gradient(135deg,#e9b878,#c98a4a);border-radius:8px"></div>
    <div class="step-text"><div class="step-num">STEP 3</div><div class="step-title">CRAS VIVERRAM</div><div class="step-body">Neque porro quisquam<br>est qui dolorem</div></div>
  </div>
</section>

<section>
  <div class="abs welcome-img" role="img" aria-label="Cardboard box holding three bags of dog food"></div>
  <h2 class="abs section-title welcome-title">Welcome to<br>Otter Bites Guild</h2>
  <p class="abs copy welcome-copy">Lorem ipsum dolor sit amet, consectetur adipiscing elit.<br>Nulla est purus, ultrices in porttitor in, accumsan non quam.<br>Nam consectetur porttitor rhoncus. Curabitur eu est et leo feugiat auctor vel quis lorem. Ut et ligula dolor, sit amet consequat lorem.<br>Aliquam porta eros sed velit imperdiet egestas</p>
  <a class="abs btn welcome-btn">Read More</a>
</section>

<section>
  <div class="abs tile" style="left:74px;background:linear-gradient(160deg,#c99a5c,#6b4a2a)" role="img" aria-label="Hands opening a gift box beside a small dog"><div class="tile-label">Vestibulum</div></div>
  <div class="abs tile" style="left:342px;background:linear-gradient(160deg,#5a4a3c,#2a2623)" role="img" aria-label="Tray of dog food with vegetables"><div class="tile-label">Vestibulum</div></div>
  <div class="abs tile" style="left:616px;background:linear-gradient(160deg,#555,#b99a6c)" role="img" aria-label="Labrador balancing a treat on its nose"><div class="tile-label">Vestibulum</div></div>
  <div class="abs tile" style="left:884px;background:linear-gradient(160deg,#f2e05a,#e6d44a)" role="img" aria-label="Dachshund on a yellow background"><div class="tile-label">Vestibulum</div></div>
</section>

<section>
  <h2 class="abs section-title inside-title">What's Inside the Box<br>Each Month</h2>
  <p class="abs copy inside-copy">Lorem ipsum dolor sit amet, consectetur adipiscing elit.<br>Nulla est purus, ultrices in porttitor in, accumsan non quam.<br>Nam consectetur porttitor rhoncus. Curabitur eu est et leo feugiat auctor vel quis lorem. Ut et ligula dolor, sit amet consequat lorem.<br>Aliquam porta eros sed velit imperdiet egestas</p>
  <a class="abs btn inside-btn">Choose Subscription&nbsp; Plans</a>
  <div class="abs inside-img" role="img" aria-label="Bone-shaped biscuits in front of a black gift box"></div>
</section>

<section>
  <div class="abs newsletter"></div>
  <div class="abs news-img" role="img" aria-label="Border collie lying beside a bowl of treats"></div>
  <h2 class="abs news-title">Subscribe to Our Newsletter</h2>
  <p class="abs news-copy">Lorem ipsum dolor sit amet, consectetur adipiscing elit ulla est purus, ultrices in porttitor in, accumsan non quam.</p>
  <div class="abs news-input">Email Address</div>
  <a class="abs btn news-btn">Subscribe Now</a>
</section>

<footer>
  <div class="abs footer"></div>
  <div class="abs foot-col" style="left:74px"><h3>The Company</h3><p>Lorem ipsum dolor sit amet, consectetur adipiscing elit ulla est purus, ultrices in porttitor in, accumsan non quam.</p></div>
  <div class="abs foot-col" style="left:381px"><h3>Site Map</h3><ul><li>Home</li><li>About Us</li><li>How &nbsp;it Works</li><li>Subscription Plan</li><li>Blog</li><li>Contact Us</li></ul></div>
  <div class="abs foot-col" style="left:614px"><h3>Customer Service</h3><ul><li>Contact Us</li><li>Sign In</li><li>Create Account</li><li>Shopping Bag</li><li>Checkout</li></ul></div>
  <div class="abs foot-col" style="left:884px"><h3>Social Media</h3></div>
  <div class="abs socials" aria-label="Social links"><span></span><span></span><span></span><span></span></div>

  <div class="abs legal"></div>
  <div class="abs legal-links">Privacy Policy<span>/</span>Terms &amp; Conditions<span>/</span>Buy Theme<span>/</span>Search Store</div>
  <div class="abs currency">USD $
    <svg class="abs" style="right:12px;top:17px" width="12" height="8" viewBox="0 0 12 8"><path d="M0 0h12L6 7z" fill="#666"/></svg>
  </div>
  <div class="abs pay" aria-label="Accepted payment methods"><span></span><span></span><span></span><span></span><span></span><span></span><span></span><span></span><span></span><span></span></div>
  <div class="abs copyright">Copyright © 2020 CompanyName All Rights Reserved.</div>
</footer>

</body>
</html>
```